Corvin Ridge Software PowerPoint template

We are a software company selling endpoint visibility, access and security technology to enterprise-level IT departments.
Our technology helps organizations gain comprehensive visibility into and control over devices accessing their corporate network so they can quickly identify and address suspicious activity on the network that could lead to potential threats like data breaches.
This technology can cost organizations upwards of $1M - depending on the size of the organization. Our primary clients are Vestral 2,000 companies.
We want a professional, polished PowerPoint template that we can use for all company presentations. Please include:
Title page
Section page
General info page
Thank you page
Logo options and color specs are attached.
Please include our tagline on at least the title page: Discover the edge. Optimize the whole.
Reason: Seeking more options. Looking for a clean design that uses lots of white space.
Software

```html
<!DOCTYPE html>
<html lang="en">
<head>
<meta charset="utf-8">
<title>Corvin Ridge Software – Title Slide</title>
<link href="https://fonts.googleapis.com/css2?family=Encode+Sans:wght@400;500;600;700&display=swap" rel="stylesheet">
<style>
  :root {
    --brand-red: #8c1b22;
    --text-grey: #6e6e6e;
    --rule-grey: #c9c9c9;
    --accent-tint: #ececec;
    --paper: #ffffff;
  }
  html, body {
    margin: 0;
    padding: 0;
    width: 1200px;
    height: 849px;
    overflow: hidden;
    background: var(--paper);
  }
  .slide {
    position: relative;
    width: 1200px;
    height: 849px;
    overflow: hidden;
    background: var(--paper);
    font-family: "Encode Sans", Arial, sans-serif;
  }
  .corner-accent {
    position: absolute;
    top: 0;
    right: 0;
    width: 380px;
    height: 360px;
    background: radial-gradient(ellipse at 100% 0%, var(--accent-tint) 0%, rgba(236,236,236,0.55) 45%, rgba(255,255,255,0) 72%);
  }
  .brand {
    position: absolute;
    left: 118px;
    top: 138px;
    display: flex;
    align-items: center;
    gap: 26px;
    color: var(--brand-red);
    font-weight: 600;
  }
  .brand-mark {
    width: 84px;
    height: 84px;
    border-radius: 50%;
    background: var(--brand-red);
  }
  .brand-name {
    display: flex;
    flex-direction: column;
    line-height: 1;
  }
  .brand-name .primary {
    font-size: 42px;
    letter-spacing: 5px;
  }
  .brand-name .secondary {
    font-size: 22px;
    letter-spacing: 19px;
    margin-top: 10px;
  }
  .tagline {
    position: absolute;
    left: 129px;
    top: 360px;
    margin: 0;
    font-weight: 400;
    font-size: 71px;
    line-height: 74px;
    color: var(--brand-red);
    letter-spacing: 0.5px;
  }
  .presenter {
    position: absolute;
    left: 130px;
    top: 558px;
    color: var(--text-grey);
  }
  .presenter .name {
    font-size: 23px;
    font-weight: 600;
    margin: 0;
  }
  .presenter .date {
    font-size: 21px;
    font-weight: 400;
    margin: 10px 0 0;
  }
  .footer-rule {
    position: absolute;
    left: 114px;
    right: 0;
    top: 769px;
    height: 1px;
    background: var(--rule-grey);
  }
  .copyright {
    position: absolute;
    left: 130px;
    top: 778px;
    font-size: 12px;
    color: #333;
  }
  .website {
    position: absolute;
    right: 75px;
    top: 778px;
    font-size: 18px;
    color: var(--brand-red);
    letter-spacing: 0.2px;
  }
  .website strong { font-weight: 700; }
</style>
</head>
<body>
<main class="slide">
  <div class="corner-accent" role="img" aria-label="Decorative pattern of light grey outlined circles in the top-right corner"></div>

  <div class="brand">
    <div class="brand-mark" aria-hidden="true"></div>
    <div class="brand-name">
      <span class="primary">CORVIN RIDGE</span>
      <span class="secondary">SOFTWARE</span>
    </div>
  </div>

  <h1 class="tagline">DISCOVER THE EDGE,<br>OPTIMIZE THE WHOLE</h1>

  <section class="presenter">
    <p class="name">NAME OF THE PRESENTEE</p>
    <p class="date">DATE : MM DD YY</p>
  </section>

  <div class="footer-rule"></div>
  <div class="copyright">©2015 Corvin Ridge Software</div>
  <div class="website">WWW. <strong>CORVINRIDGE</strong>SOFTWARE.COM</div>
</main>
</body>
</html>
```